Coastline Premier Retreats Business Card Design

Design a business card for Coastline Premier Retreats. Look at the website for colors and reference. Card should have logo, name, title, office number, mobile number, email, URL and a tagline like, "Luxury Hotel & Resort Email Marketing" (This might change).

https://www.coastlinepremierretreats.example

The rest I will leave up to your imagination.

Contact Information for Business Card

Logo, name, title, office number, mobile number, email, URL and a tagline like, "Luxury Hotel & Resort Email Marketing" (This might change).

```html
<!DOCTYPE html>
<html lang="en">
<head>
<meta charset="utf-8">
<title>Coastline Premier Retreats – Business Card</title>
<link href="https://fonts.googleapis.com/css2?family=Arimo:wght@400;700&family=Montserrat:wght@700&display=swap" rel="stylesheet">
<style>
  :root {
    --page-bg: #1b1b1b;
    --card-front: #1f1f1f;
    --card-back: #161616;
    --orange: #e8731a;
    --white: #f2f2f2;
    --emboss: #3a3a3a;
  }
  * { margin: 0; padding: 0; box-sizing: border-box; }
  html, body { width: 1200px; height: 1059px; overflow: hidden; }
  body { background: var(--page-bg); position: relative; font-family: "Arimo", Arial, sans-serif; color: var(--white); }

  .card { position: absolute; width: 690px; height: 392px; }
  .card--front { left: 256px; top: 89px; background: var(--card-front); }
  .card--back { left: 254px; top: 546px; background: var(--card-back); display: flex; align-items: center; justify-content: center; }

  .frame { position: absolute; left: 22px; top: 22px; right: 23px; top: 22px; height: 336px; border: 2px solid var(--orange); border-bottom: none; }
  .frame__base { position: absolute; bottom: 0; height: 2px; background: var(--orange); }
  .frame__base--left { left: -2px; width: 158px; }
  .frame__base--right { right: -2px; width: 158px; }

  .brand { position: absolute; left: 0; right: 0; top: 84px; text-align: center; font-family: "Montserrat", sans-serif; font-weight: 700; font-size: 30px; letter-spacing: 0.5px; color: var(--white); }
  .brand--back { position: static; color: var(--emboss); font-size: 34px; }

  .person { position: absolute; right: 365px; top: 198px; text-align: right; }
  .person__name { color: var(--orange); font-weight: 700; font-size: 28px; line-height: 32px; }
  .person__title { font-size: 16px; line-height: 20px; margin-top: 2px; letter-spacing: 0.3px; }
  .person__address { font-size: 16px; line-height: 20px; margin-top: 6px; }

  .divider { position: absolute; left: 349px; top: 203px; width: 1.5px; height: 89px; background: var(--orange); }

  .contacts { position: absolute; left: 376px; top: 200px; list-style: none; }
  .contacts li { display: flex; align-items: center; height: 25px; font-size: 15px; }
  .contacts svg { width: 12px; height: 12px; margin-right: 8px; fill: var(--orange); flex: none; }

  .tagline { position: absolute; left: 0; right: 0; top: 346px; text-align: center; font-size: 17px; }
</style>
</head>
<body>
  <section class="card card--front">
    <div class="frame">
      <span class="frame__base frame__base--left"></span>
      <span class="frame__base frame__base--right"></span>
    </div>

    <div class="brand">Coastline Premier Retreats</div>

    <div class="person">
      <p class="person__name">MARCUS HALE</p>
      <p class="person__title">CEO/Founder</p>
      <p class="person__address">Po Box, 48 Harbor Lane<br>Bayview, AB 10420</p>
    </div>

    <span class="divider"></span>

    <ul class="contacts">
      <li><svg viewBox="0 0 12 12"><path d="M3 0h6a1 1 0 0 1 1 1v10a1 1 0 0 1-1 1H3a1 1 0 0 1-1-1V1a1 1 0 0 1 1-1zm0 1.5v8h6v-8zM6 10a.6.6 0 1 0 0 1.2A.6.6 0 0 0 6 10z"/></svg>555.014.2200</li>
      <li><svg viewBox="0 0 12 12"><path d="M0 4c1-2 11-2 12 0v1.5H9V4H3v1.5H0zM2 6h8l1 5H1zm4 1.2a1.6 1.6 0 1 0 0 3.2 1.6 1.6 0 0 0 0-3.2z"/></svg>+34 600 000 412</li>
      <li><svg viewBox="0 0 12 12"><path d="M0 5 6 1l6 4v6H0zm1.2.6v4.2L4.3 7.7zm9.6 0L7.7 7.7l3.1 2.1zM1.6 10.5h8.8L6 7.5z"/></svg>info@coastlinepremierretreats.example</li>
      <li><svg viewBox="0 0 12 12"><circle cx="6" cy="6" r="6"/><path d="M3 3.5c1 0 1.5 1 2.5 1s.5 1.5-.5 2-1 2-1.5 2.5c-.5-1-1.5-2-1.5-3.5zm5 3c1 0 1.5 1 1 2s-1.5 1-2 .5.5-2.5 1-2.5z" fill="#1f1f1f"/></svg>www.coastlinepremierretreats.example</li>
    </ul>

    <p class="tagline">Luxury Hotel &amp; Resort Email Marketing</p>
  </section>

  <section class="card card--back">
    <div class="brand brand--back">Coastline Premier Retreats</div>
  </section>
</body>
</html>
```